Looking for a cool & simple business-card-design for digital agency

Hi!

We are a web agency that offers Reputation Management, Vextor & Seo Services and software development. We like cool things, we like innovative styles.

We have uploaded our logo.

Project Deadline Extended Reason: Client does not want any designs with the colorful logo. Please send us submissions ONLY with the blac and white logo. What the client would like to see:1) Back of the card: is a silver logo on a black background2) front of the card with all the data, please use white background and black logo thank you Added Friday, May 8, 2015

Industry/Entity Type

Software

```html
<!DOCTYPE html>
<html lang="en">
<head>
<meta charset="utf-8">
<title>Pixelwerk Business Card</title>
<link href="https://fonts.googleapis.com/css2?family=Open+Sans:wght@400;600;700&display=swap" rel="stylesheet">
<style>
  :root {
    --backdrop: #e4e4e4;
    --card-black: #1c1c1e;
    --card-black-soft: #2b2b2e;
    --card-white: #f7f7f5;
    --silver: #d9d9dc;
    --accent-teal: #1f9a9c;
    --ink: #2a2a2a;
    --ink-soft: #555;
    --curve-shadow: #d2d2d0;
  }
  * { margin: 0; padding: 0; box-sizing: border-box; }
  html, body {
    width: 1200px; height: 852px; overflow: hidden;
    background: var(--backdrop);
    font-family: "Open Sans", Arial, sans-serif;
  }
  .stage {
    width: 1200px; height: 852px;
    display: flex; align-items: center; justify-content: center; gap: 40px;
  }
  .card {
    position: relative;
    width: 520px; height: 300px;
    border-radius: 14px;
    overflow: hidden;
    box-shadow: 0 6px 18px rgba(0,0,0,0.18);
  }
  /* Logo side */
  .card--logo {
    background: linear-gradient(135deg, var(--card-black-soft), var(--card-black) 60%);
    display: flex; align-items: center; justify-content: center;
  }
  .wordmark {
    display: flex; align-items: center; gap: 14px;
  }
  .wordmark__square {
    width: 22px; height: 22px; background: var(--silver);
  }
  .wordmark__name {
    font-weight: 700; font-size: 46px; letter-spacing: 1px;
    color: var(--silver);
  }
  /* Contact side */
  .card--contact { background: var(--card-black); }
  .card__panel { position: absolute; inset: 0; }
  .card__mark {
    position: absolute; left: 40px; top: 130px;
    display: flex; align-items: center; gap: 10px;
  }
  .card__mark .wordmark__square { width: 16px; height: 16px; }
  .card__mark .wordmark__name { font-size: 28px; }
  .contact {
    position: absolute; left: 270px; top: 42px; width: 230px;
    color: var(--ink);
  }
  .contact__name {
    font-weight: 700; font-size: 21px; color: var(--accent-teal); line-height: 1.1;
  }
  .contact__role { font-size: 11px; color: var(--ink-soft); margin-top: 2px; }
  .contact__list { list-style: none; margin-top: 28px; }
  .contact__item {
    display: flex; align-items: center; gap: 9px;
    font-size: 13px; line-height: 20px;
  }
  .contact__icon { width: 12px; height: 12px; flex: none; fill: var(--accent-teal); }
  .contact__address { font-size: 13px; line-height: 19px; margin-top: 14px; }
</style>
</head>
<body>
<main class="stage">
  <section class="card card--logo" aria-label="Card back">
    <div class="wordmark">
      <span class="wordmark__square"></span>
      <span class="wordmark__name">Pixelwerk</span>
    </div>
  </section>

  <section class="card card--contact" aria-label="Card front">
    <svg class="card__panel" viewBox="0 0 520 300" preserveAspectRatio="none" aria-hidden="true">
      <path d="M212 0 C270 60 268 200 238 300 L520 300 L520 0 Z" fill="var(--curve-shadow)"/>
      <path d="M222 0 C282 60 280 200 252 300 L520 300 L520 0 Z" fill="var(--card-white)"/>
    </svg>
    <div class="card__mark">
      <span class="wordmark__square"></span>
      <span class="wordmark__name">Pixelwerk</span>
    </div>
    <div class="contact">
      <div class="contact__name">Your Long Name</div>
      <div class="contact__role">Managing Director</div>
      <ul class="contact__list">
        <li class="contact__item">
          <svg class="contact__icon" viewBox="0 0 12 12"><path d="M2 1h2.5l1 2.5-1.5 1a6 6 0 0 0 3.5 3.5l1-1.5 2.5 1V11C6 11 1 6 1 2z"/></svg>
          00.00.00.0000
        </li>
        <li class="contact__item">
          <svg class="contact__icon" viewBox="0 0 12 12"><path d="M3 1h6v3H3zM1 5h10v4H9v2H3V9H1zM4 8v2h4V8z"/></svg>
          00.00.00.0000
        </li>
        <li class="contact__item">
          <svg class="contact__icon" viewBox="0 0 12 12"><path d="M1 3h10v7H1zM1.5 3.5 6 7l4.5-3.5" /></svg>
          yourname@yourwebsite.com
        </li>
        <li class="contact__item">
          <svg class="contact__icon" viewBox="0 0 12 12"><circle cx="6" cy="6" r="5"/></svg>
          www.yourwebsite.com
        </li>
      </ul>
      <p class="contact__address">Your Commercial or office address<br>in just two line</p>
    </div>
  </section>
</main>
</body>
</html>
```